UPDATE 2: I HAVE ATTACHED TWO PHOTOS; PLEASE CONSIDER USING EITHER ONE IN A NEW DESIGN. THANK YOU.
UPDATE: I HAVE INCLUDED 4 SAMPLE BOOK COVERS THAT I LIKE TO HELP YOU ORIENT YOUR DESIGN WORK
Looking for book cover, spine, and back for a MEMOIR. Details:
TITLE: Mama's Quiet Orchard
AUTHOR: Lorisha Pemberfeld
GENRE: Memoir
STYLE REQUESTED: Abstract and colorful; designers are welcome to get creative. Note that the memoir takes place largely in a poor African American city.
BOOK SUMMARY: As a young girl, Lorisha Pemberfeld—or “Rishi” to her friends and family—discovers the man she thought was her father wasn’t, and her real biological father wants little if anything to do with her. What follows is the story of a girl’s longing, a longing disturbed by abuse, disappointment, and loneliness.
Set against the backdrop of Gary, Indiana—the then “murder capital of the world”—Mama’s Quiet Orchard follows Lorisha as she searches and grows, following a path that eventually leads her to self-discovery and self-confidence.
Template provided for InDesign. Please note margins and bleed areas. Make sure any letters/words are at least one inch from edges. On spine, leave three inches at bottom for publisher's logo.
Updates
To all designers: Please note that there should NOT be any images of people as part of your designs. Thank you, and my apologies for not mentioning that in the initial ask.

```html
<!DOCTYPE html>
<html lang="en">
<head>
<meta charset="utf-8">
<title>Mama’s Quiet Orchard — Lorisha Pemberfeld</title>
<link rel="stylesheet" href="https://fonts.googleapis.com/css2?family=Anton&display=swap">
<style>
  :root {
    --ink-white: #ffffff;
    --shadow: rgba(40, 10, 20, 0.6);
    --red-deep: #8a0c0a;
    --red: #c8190f;
    --orange: #ff5a12;
    --amber: #e98a2a;
    --green: #4f9a2a;
    --blue: #1565b8;
    --violet: #4a2a78;
    --maroon: #5a0a10;
  }
  * { margin: 0; padding: 0; box-sizing: border-box; }
  html, body {
    width: 779px;
    height: 1200px;
    overflow: hidden;
    background: var(--red-deep);
  }
  .cover {
    position: relative;
    width: 779px;
    height: 1200px;
    overflow: hidden;
    font-family: "Anton", "Impact", sans-serif;
    color: var(--ink-white);
  }
  .cover-art {
    position: absolute;
    inset: 0;
    background:
      radial-gradient(ellipse 150px 120px at 220px 40px, var(--orange) 0%, transparent 75%),
      radial-gradient(ellipse 220px 110px at 440px 60px, var(--maroon) 0%, transparent 75%),
      radial-gradient(ellipse 120px 160px at 740px 60px, var(--blue) 0%, transparent 75%),
      radial-gradient(ellipse 80px 200px at 20px 150px, var(--blue) 0%, transparent 75%),
      radial-gradient(ellipse 150px 200px at 110px 430px, var(--green) 0%, transparent 75%),
      radial-gradient(ellipse 200px 180px at 400px 610px, var(--green) 0%, transparent 70%),
      radial-gradient(ellipse 170px 260px at 690px 420px, var(--red-deep) 0%, transparent 75%),
      radial-gradient(ellipse 260px 110px at 480px 810px, var(--blue) 0%, transparent 75%),
      radial-gradient(ellipse 150px 120px at 110px 790px, var(--orange) 0%, transparent 75%),
      radial-gradient(ellipse 130px 150px at 620px 790px, var(--amber) 0%, transparent 75%),
      radial-gradient(ellipse 140px 220px at 60px 1060px, var(--blue) 0%, transparent 75%),
      radial-gradient(ellipse 150px 180px at 720px 1100px, var(--blue) 0%, transparent 75%),
      radial-gradient(ellipse 220px 120px at 420px 1170px, var(--red) 0%, transparent 75%),
      linear-gradient(160deg, var(--red) 0%, var(--red-deep) 45%, var(--red) 70%, var(--violet) 100%);
  }
  .line {
    position: absolute;
    left: 0;
    width: 100%;
    text-align: center;
    line-height: 1;
    text-transform: uppercase;
    text-shadow: 4px 6px 8px var(--shadow);
    white-space: nowrap;
  }
  .title-line { font-size: 152px; }
  .title-line--1 { top: 132px; }
  .title-line--2 { top: 279px; }
  .title-line--3 { top: 425px; }
  .subtitle {
    top: 666px;
    font-size: 50px;
    letter-spacing: 0.03em;
    word-spacing: 0.25em;
  }
  .author-line { font-size: 116px; }
  .author-line--1 { top: 815px; }
  .author-line--2 { top: 953px; }
</style>
</head>
<body>
  <main class="cover">
    <div class="cover-art" role="img" aria-label="Abstract painted background in layered reds, oranges, greens and blues with scratched lines and silhouettes of birds in flight"></div>
    <h1 class="book-title">
      <span class="line title-line title-line--1">Mama’s</span>
      <span class="line title-line title-line--2">Quiet</span>
      <span class="line title-line title-line--3">Orchard</span>
    </h1>
    <p class="line subtitle">A Memoir</p>
    <p class="book-author">
      <span class="line author-line author-line--1">Lorisha</span>
      <span class="line author-line author-line--2">Pemberfeld</span>
    </p>
  </main>
</body>
</html>
```